Business Card design for law firm = Brightvale Australia

We are seeking a new design for our business cards.
We are keeping our logo, which is attached.
We need space for
Name
Title
Address is , which is
Level 7
214 Marlowe Street
Sydney NSW 2047
Phone :
Mobile :
Fax :
Email :
DX :
website www.brightvale-example.com.au

Industry/Entity Type

Law Firm / Banking and Finance

Contact Information for Business Card

We are seeking a new design for our business cards. We are keeping our logo. We need space for Name Title Address is Level 7 214 Marlowe Street Sydney NSW 2047 Phone Mobile Fax Email DX website www.brightvale-example.com.au

Colors
0054AA
0677BA
7BADD7
CADEEF
E8F1F8

Requirements
Must have
• see our website for general feel www.brightvale-example.com.au

```html
<!DOCTYPE html>
<html lang="en">
<head>
<meta charset="utf-8">
<title>Brightvale Australia – Business Card</title>
<link rel="stylesheet" href="https://fonts.googleapis.com/css2?family=Tinos&family=Arimo:wght@400&display=swap">
<style>
  :root{
    --navy:#0054AA;
    --blue:#0677BA;
    --sky:#06A3DA;
    --mist:#7BADD7;
    --pale:#CADEEF;
    --wash:#E8F1F8;
    --ink:#1b1b1b;
    --white:#ffffff;
    --stage:#d4d4d4;
  }
  *{box-sizing:border-box;margin:0;padding:0}
  html,body{width:1200px;height:900px;overflow:hidden}
  body{background:var(--stage);font-family:"Arimo",Arial,sans-serif;color:var(--ink)}
  .stage{width:1200px;height:900px;display:flex;flex-direction:column;align-items:center;justify-content:center;gap:46px}
  .card{width:680px;height:389px;border-radius:26px;position:relative;overflow:hidden;box-shadow:0 4px 10px rgba(0,0,0,.25)}

  /* brand name set in the card's text face */
  .brand-name{font-family:"Arimo",Arial,sans-serif;font-weight:400;line-height:1;white-space:nowrap}

  /* front */
  .card--front{background:linear-gradient(180deg,var(--sky) 0%,var(--blue) 100%);display:flex;align-items:center;justify-content:center}
  .card--front .brand-name{color:var(--white);font-size:56px}

  /* back */
  .card--back{background:var(--white)}
  .card--back .brand-name{position:absolute;left:44px;top:62px;color:var(--blue);font-size:44px}

  .contact-list{position:absolute;left:44px;bottom:36px;list-style:none;display:flex;flex-direction:column;gap:6px}
  .contact-list li{display:flex;align-items:center;gap:10px;font-size:17px;line-height:1}
  .contact-icon{width:22px;height:22px;background:var(--sky);display:flex;align-items:center;justify-content:center;flex:none}
  .contact-icon svg{width:14px;height:14px}

  .detail-panel{position:absolute;right:0;top:40px;width:290px;height:255px;background:var(--wash);padding:34px 34px 0 0;text-align:right}
  .person__name{font-family:"Tinos","Times New Roman",serif;color:var(--navy);font-size:30px;line-height:1.05}
  .person__title{color:var(--sky);font-size:15px;margin-top:2px}
  .dx{color:var(--navy);font-size:16px;margin-top:16px}
  .address{font-style:normal;font-size:16px;line-height:1.35;margin-top:16px}
</style>
</head>
<body>
<main class="stage">

  <section class="card card--front" aria-label="Card front">
    <p class="brand-name">Brightvale</p>
  </section>

  <section class="card card--back" aria-label="Card back">
    <p class="brand-name">Brightvale</p>

    <ul class="contact-list">
      <li><span class="contact-icon"><svg viewBox="0 0 16 16" fill="none" stroke="#fff" stroke-width="1.6"><path d="M4 2l2 3-1.5 1.5a8 8 0 005 5L11 10l3 2-1.5 2.5C7 14 2 9 1.5 3.5z"/></svg></span>044-555 010 247</li>
      <li><span class="contact-icon"><svg viewBox="0 0 16 16" fill="none" stroke="#fff" stroke-width="1.6"><rect x="4" y="1.5" width="8" height="13" rx="1.2"/><path d="M7 12.5h2"/></svg></span>044-555 010 248</li>
      <li><span class="contact-icon"><svg viewBox="0 0 16 16" fill="none" stroke="#fff" stroke-width="1.6"><rect x="4" y="1.5" width="8" height="5"/><rect x="1.5" y="6.5" width="13" height="6"/><rect x="4" y="10" width="8" height="4.5" fill="#fff"/></svg></span>044-555 010 249</li>
      <li><span class="contact-icon"><svg viewBox="0 0 16 16" fill="none" stroke="#fff" stroke-width="1.6"><rect x="1.5" y="3.5" width="13" height="9"/><path d="M1.5 3.5L8 9l6.5-5.5"/></svg></span>info@brightvale-example.com</li>
      <li><span class="contact-icon"><svg viewBox="0 0 16 16" fill="none" stroke="#fff" stroke-width="1.4"><circle cx="8" cy="8" r="6.2"/><ellipse cx="8" cy="8" rx="2.6" ry="6.2"/><path d="M1.8 8h12.4"/></svg></span>www.brightvale-example.com.au</li>
    </ul>

    <div class="detail-panel">
      <p class="person__name">Daniel Hartley</p>
      <p class="person__title">Managing Director</p>
      <p class="dx">DX :204718</p>
      <address class="address">Level 7, 214 Marlowe Street<br>Sydney NSW 2047</address>
    </div>
  </section>

</main>
</body>
</html>
```